Fitness Business Card Design Needed

We are looking for a business card design that stands out but is also simple and unique. I like the idea of on one side using the picture of myself with my logo at my feet. I love the texture on the business card so please take that into account when designing. Then on the other side having my contact details. I want it to be clean, modern, and pretty. I am open to designs that allow spot gloss or gold foiling.

Contact Information for Business Card

Space for Name, Phone number, email, and website

```html
<!DOCTYPE html>
<html lang="en">
<head>
<meta charset="UTF-8">
<title>Petite Power Fitness – Business Card</title>
<link href="https://fonts.googleapis.com/css2?family=Montserrat:wght@300;400;500&display=swap" rel="stylesheet">
<style>
  :root {
    --page: #e9e6e1;
    --card: #0c0c0c;
    --card-edge: #1a1a1a;
    --gold: #d6a64e;
    --white: #f2f2f2;
    --emboss: #1f1f1f;
    --emboss-light: #2b2b2b;
  }
  * { margin: 0; padding: 0; box-sizing: border-box; }
  html, body {
    width: 1200px; height: 1200px; overflow: hidden;
    background: var(--page);
    font-family: "Montserrat", sans-serif;
  }
  .canvas {
    position: relative; width: 1200px; height: 1200px;
    display: flex; flex-direction: column; align-items: center; justify-content: center; gap: 60px;
  }
  .card {
    position: relative; width: 900px; height: 514px;
    background: var(--card);
    border: 1px solid var(--card-edge);
    box-shadow: 0 14px 30px rgba(0,0,0,0.25);
    overflow: hidden;
  }

  /* Shared wordmark */
  .brand {
    position: absolute;
    display: flex; flex-direction: column; align-items: center; gap: 14px;
    white-space: nowrap;
  }
  .brand-mark { border: 1.5px solid currentColor; }

  /* Back side */
  .card-back .brand {
    left: 50%; top: 50%; transform: translate(-50%, -50%);
    color: var(--emboss-light);
  }
  .card-back .brand-mark { width: 90px; height: 90px; }
  .card-back .brand-name {
    font-weight: 400; font-size: 24px; letter-spacing: 7px; color: var(--emboss);
    text-shadow: 0 1px 0 var(--emboss-light);
  }

  /* Front side */
  .portrait {
    position: absolute; left: 50px; bottom: 0; width: 250px; height: 440px;
    background: radial-gradient(ellipse at 50% 45%, #c98a6a 0%, #a45c45 35%, #3a2520 70%, rgba(12,12,12,0) 90%);
    opacity: 0.9;
  }
  .card-front .brand {
    left: 460px; top: 310px; transform: translateX(-50%);
    color: var(--gold);
  }
  .card-front .brand-mark { width: 60px; height: 60px; }
  .card-front .brand-name {
    font-weight: 400; font-size: 14px; letter-spacing: 4px; color: var(--gold);
  }
  .identity {
    position: absolute; right: 60px; top: 56px; text-align: right;
  }
  .identity .name {
    font-size: 36px; font-weight: 400; letter-spacing: 1px; color: var(--gold);
  }
  .identity .role {
    font-size: 17px; font-weight: 300; color: var(--white); margin-top: 4px;
  }
  .contacts {
    position: absolute; right: 60px; top: 180px; list-style: none;
    display: flex; flex-direction: column; gap: 6px; align-items: flex-end;
  }
  .contacts li {
    display: flex; align-items: center; gap: 10px;
    font-size: 16px; font-weight: 300; color: var(--white);
  }
  .contacts svg { width: 15px; height: 15px; fill: none; stroke: var(--gold); stroke-width: 1.8; }
</style>
</head>
<body>
<main class="canvas">

  <section class="card card-back" aria-label="Card back">
    <div class="brand">
      <div class="brand-mark"></div>
      <div class="brand-name">PETITE POWER FITNESS</div>
    </div>
  </section>

  <section class="card card-front" aria-label="Card front">
    <div class="portrait" role="img" aria-label="Full-length photo of the trainer standing in a red swimsuit on a small patch of sand"></div>

    <div class="brand">
      <div class="brand-mark"></div>
      <div class="brand-name">PETITE POWER FITNESS</div>
    </div>

    <div class="identity">
      <div class="name">NORA VALE</div>
      <div class="role">Manager</div>
    </div>

    <ul class="contacts">
      <li>555 014 2286
        <svg viewBox="0 0 16 16"><rect x="4" y="1" width="8" height="14" rx="1.5"/><line x1="7" y1="12.5" x2="9" y2="12.5"/></svg>
      </li>
      <li>555 019 3341
        <svg viewBox="0 0 16 16"><path d="M3 2l3 1 1 3-2 1.5a9 9 0 0 0 3.5 3.5L10 9l3 1 1 3-2 1.5C7 14 2 9 1.5 4z"/></svg>
      </li>
      <li>petitepowerfit@mail.com
        <svg viewBox="0 0 16 16"><rect x="1.5" y="3.5" width="13" height="9"/><path d="M1.5 3.5l6.5 5 6.5-5"/></svg>
      </li>
      <li>www.petitepowerfit.com
        <svg viewBox="0 0 16 16"><circle cx="8" cy="8" r="6.5"/><ellipse cx="8" cy="8" rx="3" ry="6.5"/><line x1="1.5" y1="8" x2="14.5" y2="8"/></svg>
      </li>
    </ul>
  </section>

</main>
</body>
</html>
```